business card deign

Logo needs the following on it.
1. attached logo
2. Tagline - "If it keeps a snack fresh or the picnic rolling...we make it!"
3. Name- Dalton Pikes, Founder and CPO
4. Address - 412 E. Carver Avenue, Ste 2207, Harbor Vale, GA. 33917
5. Phone - 555.318.4726

```html
<!DOCTYPE html>
<html lang="en">
<head>
<meta charset="utf-8">
<title>Brimway Business Card</title>
<link rel="stylesheet" href="https://fonts.googleapis.com/css2?family=Roboto:wght@400;500;700;900&display=swap">
<style>
  :root {
    --page-bg: #e6d6c6;
    --card-white: #ffffff;
    --ink: #111111;
    --ink-soft: #1a1a1a;
    --emboss: #e4e4e4;
    --shadow: rgba(60, 40, 20, 0.28);
  }
  * { box-sizing: border-box; margin: 0; padding: 0; }
  html, body {
    width: 1200px;
    height: 711px;
    overflow: hidden;
    background: var(--page-bg);
    font-family: "Roboto", Arial, sans-serif;
    color: var(--ink);
  }
  .stage {
    width: 1200px;
    height: 711px;
    display: flex;
    align-items: center;
    justify-content: center;
    gap: 44px;
  }
  .card {
    position: relative;
    width: 536px;
    height: 306px;
    background: var(--card-white);
    border-radius: 18px;
    overflow: hidden;
    box-shadow: 0 14px 30px var(--shadow);
  }

  /* Back side */
  .card--back {
    display: flex;
    align-items: center;
    justify-content: center;
  }
  .back-wordmark {
    font-weight: 700;
    font-size: 46px;
    letter-spacing: 22px;
    padding-left: 22px;
    color: var(--emboss);
  }

  /* Front side */
  .front-art {
    position: absolute;
    top: 0;
    right: 0;
    width: 44%;
    height: 100%;
    background: linear-gradient(100deg, var(--card-white) 0%, var(--card-white) 38%, var(--ink-soft) 72%, var(--ink-soft) 100%);
  }
  .front-info {
    position: absolute;
    left: 0;
    top: 34px;
    width: 62%;
  }
  .wordmark {
    display: flex;
    align-items: center;
    gap: 10px;
    margin-left: 34px;
    font-weight: 700;
    font-size: 24px;
    letter-spacing: 10px;
  }
  .wordmark-dot {
    width: 14px;
    height: 14px;
    background: var(--ink);
  }
  .name-block {
    position: relative;
    margin-top: 26px;
    padding-left: 34px;
  }
  .name-block::before {
    content: "";
    position: absolute;
    left: 0;
    top: 4px;
    width: 16px;
    height: 50px;
    background: var(--ink);
  }
  .person-name {
    font-weight: 700;
    font-size: 30px;
    line-height: 1.05;
  }
  .person-role {
    font-weight: 500;
    font-size: 16px;
    margin-top: 4px;
  }
  .tagline {
    margin: 16px 0 0 34px;
    font-size: 13px;
    line-height: 1.4;
    font-weight: 500;
    max-width: 250px;
  }
  .contact {
    list-style: none;
    margin: 14px 0 0 34px;
    font-size: 13px;
    font-weight: 500;
    line-height: 1.4;
  }
  .contact li {
    display: flex;
    gap: 8px;
    align-items: flex-start;
  }
  .contact svg {
    width: 14px;
    height: 14px;
    flex: none;
    margin-top: 2px;
  }
</style>
</head>
<body>
<main class="stage">
  <section class="card card--back" aria-label="Card back">
    <div class="back-wordmark">BRIMWAY</div>
  </section>

  <section class="card card--front" aria-label="Card front">
    <div class="front-art" role="img" aria-label="Large white kangaroo illustration set against a black corner"></div>
    <div class="front-info">
      <div class="wordmark"><span class="wordmark-dot"></span>BRIMWAY</div>
      <div class="name-block">
        <h1 class="person-name">Dalton Pikes</h1>
        <p class="person-role">Founder and CPO</p>
      </div>
      <p class="tagline">If it keeps a snack fresh or the picnic rolling...we make it!</p>
      <ul class="contact">
        <li>
          <svg viewBox="0 0 24 24" aria-hidden="true"><path fill="currentColor" d="M6.6 10.8a15.1 15.1 0 0 0 6.6 6.6l2.2-2.2a1 1 0 0 1 1-.25 11.4 11.4 0 0 0 3.6.57 1 1 0 0 1 1 1V20a1 1 0 0 1-1 1A17 17 0 0 1 3 4a1 1 0 0 1 1-1h3.5a1 1 0 0 1 1 1c0 1.25.2 2.45.57 3.6a1 1 0 0 1-.25 1z"/></svg>
          <span>555.318.4726</span>
        </li>
        <li>
          <svg viewBox="0 0 24 24" aria-hidden="true"><path fill="currentColor" d="M12 2a7 7 0 0 0-7 7c0 5.2 7 13 7 13s7-7.8 7-13a7 7 0 0 0-7-7zm0 9.5A2.5 2.5 0 1 1 12 6.5a2.5 2.5 0 0 1 0 5z"/></svg>
          <span>412 E. Carver Avenue,<br>Ste 2207, Harbor Vale, GA. 33917</span>
        </li>
      </ul>
    </div>
  </section>
</main>
</body>
</html>
```